Catalogue Design Project

We need a catalog design for a new private university called Redwell Institute Bayshore (see website www.rwi-bs.org). The catalog should be about 30 pages maximum and will include items such as General Information, Academic schedule, department descriptions, program descriptions, course descriptions, school policies, student services, admissions, San diego Lifestyle, etc.
I will provide the text but I need a professional design with regard to page layouts. I have provided some examples.
Ok, i posted the catalog content, just missing course descriptions.
Target Market(s)
Young Professionals, Foreign Students
Industry/Entity Type
University
Look and feel
Each slider illustrates characteristics of the customer's brand and the style your logo design should communicate.

```html
<!DOCTYPE html>
<html lang="en">
<head>
<meta charset="utf-8">
<title>Redwell Institute Bayshore – Our Mission</title>
<link href="https://fonts.googleapis.com/css2?family=Arimo&family=Open+Sans:wght@500&display=swap" rel="stylesheet">
<style>
  :root {
    --navy: #1f1b62;
    --violet: #5656b8;
    --violet-light: #7c7ee2;
    --green-text: #3f8a45;
    --mint: #b2dcb4;
    --forest: #4b8d57;
    --ink: #141264;
    --rose: #c98478;
    --photo-tone: #a9a796;
    --white: #ffffff;
  }
  * { margin: 0; padding: 0; box-sizing: border-box; }
  html, body { width: 927px; height: 1200px; overflow: hidden; background: var(--white); }
  .page { position: relative; width: 927px; height: 1200px; overflow: hidden; background: var(--white); }

  .side-strip {
    position: absolute; left: 0; top: 0; width: 58px; height: 1200px;
    background: linear-gradient(180deg, var(--navy) 0%, var(--navy) 45%, #3b3590 80%, #5a4d9a 100%);
  }
  .swoosh { position: absolute; right: 0; top: 0; width: 260px; height: 900px; }

  .mission-title {
    position: absolute; left: 58px; width: 740px; top: 30px;
    font-family: "Open Sans", sans-serif; font-weight: 500;
    font-size: 41px; color: var(--green-text); text-align: center; letter-spacing: 0.5px;
  }
  .mission-text {
    position: absolute; left: 124px; top: 100px; width: 678px;
    font-family: "Arimo", Arial, sans-serif; font-size: 26.5px; line-height: 36.2px;
    color: var(--green-text); text-align: justify;
  }

  .campus-photo {
    position: absolute; left: 58px; top: 548px; width: 753px; height: 423px;
    background: var(--photo-tone);
  }

  .contact-band {
    position: absolute; left: 58px; top: 971px; width: 869px; height: 206px;
    background: var(--mint);
  }
  .ornament {
    position: absolute; top: 1040px; width: 130px; height: 150px;
    background: var(--rose); opacity: 0.35; border-radius: 40% 60% 50% 50%;
  }
  .ornament--left { left: 0; }
  .ornament--right { right: 0; }

  .contact {
    position: absolute; left: 58px; width: 753px; top: 985px;
    font-family: "Arimo", Arial, sans-serif; color: var(--ink); text-align: center;
  }
  .contact-heading { font-size: 27px; font-weight: 400; line-height: 32px; margin-bottom: 6px; }
  .contact-line { font-size: 19.5px; line-height: 31.5px; }

  .footer-bar {
    position: absolute; left: 58px; top: 1177px; width: 869px; height: 23px;
    background: var(--forest);
  }
  .footer-url {
    position: absolute; left: 58px; width: 753px; top: 1177px; height: 23px;
    font-family: "Arimo", Arial, sans-serif; font-size: 17px; line-height: 23px;
    color: var(--ink); text-align: center;
  }
</style>
</head>
<body>
<div class="page">
  <div class="side-strip"></div>

  <svg class="swoosh" viewBox="0 0 260 900" aria-hidden="true">
    <defs>
      <linearGradient id="swooshFill" x1="0" y1="0" x2="1" y2="1">
        <stop offset="0" stop-color="#4c4aa6"/>
        <stop offset="0.6" stop-color="#6466c8"/>
        <stop offset="1" stop-color="#7c7ee2"/>
      </linearGradient>
    </defs>
    <path d="M72 0 H260 V578 C210 540 180 470 190 380 C200 280 210 190 160 120 C130 80 60 60 0 58 C30 40 55 20 72 0 Z" fill="url(#swooshFill)"/>
    <path d="M260 618 V860 C215 830 200 760 212 700 C222 660 240 635 260 618 Z" fill="url(#swooshFill)"/>
  </svg>

  <h1 class="mission-title">OUR MISSION</h1>
  <p class="mission-text">"The mission of Redwell Institute Bayshore is to provide students with the finest education and training necessary to enter the real world and hit the ground running. We offer intense English fluency programs aimed to achieve language proficiency in the shortest time possible by creating a customized schedule for students to progress by completing activities inside and outside of the classroom. Our business programs, taught by leaders in the industry, are designed with the strict intent of aiding students narrow their focus and show them the avenues by which to achieve their life goals."</p>

  <div class="campus-photo" role="img" aria-label="Photo of a historic stone campus building"></div>

  <div class="contact-band"></div>
  <div class="ornament ornament--left" role="img" aria-label="Decorative leaf sprig"></div>
  <div class="ornament ornament--right" role="img" aria-label="Decorative leaf sprig"></div>

  <div class="contact">
    <h2 class="contact-heading">Contact Us</h2>
    <p class="contact-line">Address Line 1,text</p>
    <p class="contact-line">Address Line 2,</p>
    <p class="contact-line">Address Line 3,</p>
    <p class="contact-line">Address Line 4 - 0000000</p>
  </div>

  <div class="footer-bar"></div>
  <p class="footer-url">http://www.rwi-bs.org</p>
</div>
</body>
</html>
```